Brenwick Coaching Website

I would like someone to design my website. I have an existing site which is really basic and needs an overhaul. I have attached a powerpoint with all the information I require. I am flexible with the design and layout and am ok with graphics being added to enhance the attractiveness of the site.

```html
<!DOCTYPE html>
<html lang="en">
<head>
<meta charset="utf-8">
<title>Brenwick Coaching</title>
<link rel="stylesheet" href="https://fonts.googleapis.com/css2?family=Oxygen:wght@300;400&display=swap">
<style>
  :root {
    --orange: #ef5a2a;
    --blue: #1f6fbf;
    --blue-light: #3a8fd6;
    --blue-dark: #0f4f9e;
    --text: #4a4a4a;
    --muted: #6b6b6b;
    --rule: #e6e6e6;
    --footer-bg: #fafafa;
    --card-bg: #f4f4f4;
    --white: #ffffff;
  }
  * { box-sizing: border-box; margin: 0; padding: 0; }
  html, body { width: 1200px; height: 1020px; overflow: hidden; background: var(--white); }
  body { font-family: "Oxygen", Arial, sans-serif; color: var(--text); position: relative; border-top: 5px solid var(--rule); }
  .brand { position: absolute; left: 60px; top: 58px; font-size: 40px; font-weight: 400; color: var(--blue); letter-spacing: -0.5px; }
  .contact { position: absolute; right: 76px; top: 58px; text-align: right; }
  .contact .phone { font-size: 31px; font-weight: 300; color: var(--orange); line-height: 1.2; }
  .contact .email { font-size: 17px; color: var(--blue); margin-top: 6px; }
  .hero { position: absolute; left: 56px; top: 152px; width: 1087px; height: 428px; border: 1px solid #cfcfcf; border-radius: 4px; overflow: hidden; background: linear-gradient(100deg, #6d5a4a 0%, #d9cfc4 30%, #efe9e2 48%, #5b5550 70%, #2f2f33 100%); }
  .hero-nav { position: absolute; top: 198px; width: 72px; height: 72px; border-radius: 50%; background: rgba(255,255,255,0.25); border: 2px solid rgba(255,255,255,0.35); }
  .hero-nav.prev { left: 4px; }
  .hero-nav.next { right: 4px; }
  .hero-dots { position: absolute; left: 50%; bottom: 11px; transform: translateX(-50%); display: flex; gap: 4px; }
  .hero-dots span { width: 13px; height: 13px; border-radius: 50%; background: #111; }
  .hero-dots span.active { background: var(--white); }
  .side-nav { position: absolute; left: 57px; top: 612px; width: 286px; height: 244px; border-radius: 2px; background: linear-gradient(180deg, var(--blue-light), var(--blue-dark)); padding: 10px 26px 0; }
  .side-nav a { display: block; color: var(--white); text-decoration: none; font-size: 17.5px; line-height: 53px; padding-left: 16px; border-bottom: 1px solid rgba(255,255,255,0.22); }
  .side-nav a:last-child { border-bottom: none; }
  .intro { position: absolute; left: 377px; top: 626px; width: 530px; }
  .intro h1 { font-size: 28px; font-weight: 400; color: var(--orange); margin-bottom: 8px; }
  .intro p { font-size: 16px; line-height: 26.5px; color: var(--text); margin-bottom: 5px; }
  .intro .cta { display: block; margin-top: 36px; color: var(--orange); font-size: 18px; text-decoration: none; }
  .profile { position: absolute; left: 938px; top: 612px; width: 205px; height: 265px; border: 1px solid #d8d8d8; border-radius: 3px; overflow: hidden; background: var(--card-bg); }
  .profile .photo { height: 220px; background: linear-gradient(180deg, #9b8f82 0%, #c7b8a9 45%, #d98b76 100%); }
  .profile .label { text-align: center; line-height: 44px; font-size: 18px; color: #555; }
  .footer { position: absolute; left: 0; right: 0; top: 920px; height: 100px; border-top: 1px solid var(--rule); background: var(--footer-bg); }
  .footer .legal { position: absolute; left: 60px; top: 32px; font-size: 14px; color: var(--muted); }
  .social { position: absolute; right: 62px; top: 28px; display: flex; gap: 8px; }
  .social span { width: 24px; height: 24px; border-radius: 2px; }
  .social .s1 { background: #3b5998; }
  .social .s2 { background: #39b0e6; }
  .social .s3 { background: #1a6da8; }
  .social .s4 { background: #f2861f; }
</style>
</head>
<body>
  <header>
    <div class="brand">Brenwick Coaching</div>
    <div class="contact">
      <div class="phone">1300 555 210</div>
      <div class="email">Maren.Holt@brwkcoaching.com</div>
    </div>
  </header>

  <section class="hero" role="img" aria-label="Photo of three business people in a coaching conversation at a table">
    <span class="hero-nav prev"></span>
    <span class="hero-nav next"></span>
    <div class="hero-dots"><span class="active"></span><span></span><span></span><span></span></div>
  </section>

  <nav class="side-nav">
    <a href="#">Invididula Coaching (1)</a>
    <a href="#">Group Work (2)</a>
    <a href="#">Resources (3)</a>
    <a href="#">Inspiration Booth (5)</a>
  </nav>

  <main class="intro">
    <h1>Welcome to Brenwick Coaching Website</h1>
    <p>Welcome to BRWK Coaching where we put a new prespective on the way you work, live and play.</p>
    <p>Through our programs you will learn new skills &amp; techniques to enable you to break through the barriers that have kept you from reaching your full potential up to now.</p>
    <a class="cta" href="#">Get your free 30 minute introductory coaching session (4)</a>
  </main>

  <aside class="profile">
    <div class="photo" role="img" aria-label="Portrait photo of the coach outdoors"></div>
    <div class="label">About Maren (6)</div>
  </aside>

  <footer class="footer">
    <div class="legal">© 2014 Company Name&nbsp; All right reserved&nbsp; Term of Use</div>
    <div class="social" aria-label="Social links">
      <span class="s1"></span><span class="s2"></span><span class="s3"></span><span class="s4"></span>
    </div>
  </footer>
</body>
</html>
```